Ashmoor Web Design Project

I need the front page and an internal page designed for this client's website. The logo is attached. Obviously the colors have to go with and/or work with the logo colors. I also attached a very rough brochure layout to help you see the direction we're going in with print materials. The rough site map is also attached. I see a slider on the homepage, the art for which I may come back to you to create. This clinic is in a very high end Dallas neighborhood. The hook is that it's a primary care and urgent facility with convenient hours.

I don't know how much this impacts your design, but this will be a Wordpress site and I'm using a framework called Brovila (brovila.com). If Brovila proves to be inflexible, I'll have to get a template that allows me to execute your design.

This site (http://lanternvaleclinic.com) has the type and quality of content I will eventually have on the Ashmoor site.

I just revised the brief for this project. I added the site map and added details to the overview and the "Must Have" section. Thank you for revisiting the brief. 

Reason: Christmas was a bad time to end it.

Target Market(s)

Women 25-54 with children living at home, income over $150k/year

Industry/Entity Type

Clinic

Requirements
Must have
• Masthead incorporating the logo
Followed by the primary nav
Slider on the home page below that
Dual nav - 1 with the nav in the attached site map
2 secondary nav with areas of healthcare
There will three blocks under the nav
1. It's about time (with a small blurb less than 50 words.
2. It's about choices (with small blurb)
3. It's about you (with small blurb)
Three footer blocks
patient check in link on every page
"No appointment? No problem" icon on every page

```html
<!DOCTYPE html>
<html lang="en">
<head>
<meta charset="utf-8">
<title>Ashmoor Medical</title>
<link href="https://fonts.googleapis.com/css2?family=Montserrat:wght@500;600;700&family=Open+Sans:wght@400;600&display=swap" rel="stylesheet">
<style>
:root{
  --blue:#0a5c9f;
  --blue-dark:#084f8a;
  --green:#1daa55;
  --sky:#4a90e2;
  --grey:#9a9a9a;
  --text:#333;
  --stripe:repeating-linear-gradient(135deg,#1daa55 0 2px,#fff 2px 4px);
}
*{margin:0;padding:0;box-sizing:border-box}
html,body{width:1200px;height:1002px;overflow:hidden;background:#fff}
body{position:relative;font-family:"Open Sans",Arial,sans-serif;color:var(--text)}
.abs{position:absolute}

/* masthead */
.logo{left:212px;top:10px;display:flex;align-items:center;gap:10px}
.logo-mark{width:64px;height:64px;border-radius:50%;background:var(--blue)}
.logo-name{font-family:"Montserrat",sans-serif;font-weight:700;font-size:38px;color:var(--blue);line-height:1}
.logo-tag{font-family:"Montserrat",sans-serif;font-weight:600;font-size:12.5px;color:#444;margin-top:4px;text-align:center}
.top-links{left:712px;top:18px;font-size:10px;color:var(--blue)}
.top-links span{margin:0 5px;color:#555}
.social{display:flex;gap:6px}
.social i{display:block;width:23px;height:23px;border-radius:50%;background:var(--green)}
.social.top{left:901px;top:17px}
.phone{left:826px;top:48px;font-family:"Montserrat",sans-serif;font-weight:600;font-size:22px;color:var(--blue)}

/* nav */
.stripe{height:5px;background:var(--stripe)}
.navbar{left:0;top:90px;width:1200px;height:52px;background:linear-gradient(#fff,#f0f0f0)}
.navbar .stripe.b{position:absolute;bottom:0;width:100%}
.navbar ul{list-style:none}
.navbar li{position:absolute;top:18px;font-family:"Montserrat",sans-serif;font-weight:600;font-size:14.5px;color:var(--blue)}

/* side menu */
.side{left:218px;top:175px;width:196px;height:224px;background:var(--blue);border:3px solid transparent;border-image:var(--stripe) 3}
.side ul{list-style:none;padding-top:2px}
.side li{height:28.8px;line-height:28.8px;padding-left:18px;font-family:"Open Sans",sans-serif;font-weight:400;font-size:14px;color:#fff;border-bottom:2px dotted #3fb86c;white-space:nowrap}
.side li:last-child{border:none}
.side-tail{left:240px;top:399px}

/* hero */
.hero-photo{left:792px;top:164px;width:216px;height:248px;border-radius:8px;background:radial-gradient(circle at 45% 45%,#d8c4ad,#eef1f4 70%,#fff);z-index:0}
.hero-line{left:428px;font-family:"Montserrat",sans-serif;font-weight:700;white-space:nowrap;color:var(--blue);line-height:1.2;z-index:1}
.dots{left:585px;top:408px;display:flex;gap:3px}
.dots i{width:10px;height:10px;border-radius:50%;background:var(--blue)}
.dots i:first-child{background:var(--green)}

/* feature blocks */
.block{top:453px;width:247px;height:237px;border:6px solid transparent;border-image:var(--stripe) 6;background:linear-gradient(#fff 40%,#eee 60%,#fff 75%)}
.block h2{margin-top:16px;text-align:center;font-family:"Montserrat",sans-serif;font-weight:600;font-size:20px;color:var(--blue)}
.block h2 em{font-style:normal;color:var(--green)}
.block .icon{width:92px;height:92px;border-radius:50%;margin:12px auto 0;display:flex;align-items:center;justify-content:center}
.block p{margin:17px 20px 0 20px;font-size:9.5px;line-height:14.7px;color:#333}
.more{display:block;margin:6px auto 0;width:52px;height:16px;border:1px solid var(--blue);transform:skewX(-15deg);text-align:center;font-family:"Montserrat",sans-serif;font-size:10px;line-height:14px;color:var(--blue)}

/* about */
.about-title{left:213px;top:716px;font-family:"Montserrat",sans-serif;font-weight:600;font-size:21px;color:var(--blue);white-space:nowrap}
.about-title em{font-style:normal;color:var(--green)}
.about-sub{left:466px;top:720px;font-family:"Montserrat",sans-serif;font-weight:600;font-size:17px;color:var(--grey);white-space:nowrap}
.about-copy{left:213px;top:756px;width:600px;font-size:10.8px;line-height:17px;color:#333;font-family:Arial,sans-serif}
.doc-photo{left:851px;top:723px;width:109px;height:107px;border:3px solid #888;background:linear-gradient(#aaa,#ddd)}
.doc-name{left:840px;top:834px;font-family:"Montserrat",sans-serif;font-weight:600;font-size:12px;color:var(--blue)}

/* footer */
.footer-stripe{left:0;top:895px;width:1200px}
.footer-bg{left:0;top:900px;width:1200px;height:102px;background:linear-gradient(#fff 60%,#e8e8e8)}
.foot-links{left:218px;top:920px;font-size:10px;color:#333}
.foot-links span{margin-right:11px}
.counters{left:213px;top:947px;display:flex;gap:12px}
.counter{display:flex;gap:3px}
.counter i{width:36px;height:15px;border:1px solid #ccc;border-radius:2px;background:#eef2f8}
.counter b{font-weight:400;font-size:8px;line-height:15px;padding:0 4px;border:1px solid #ccc;color:#333}
.social.foot{left:632px;top:921px}
.foot-logo{left:740px;top:912px;display:flex;align-items:center;gap:6px}
.foot-logo .logo-mark{width:36px;height:36px}
.foot-logo .logo-name{font-size:22px}
.foot-logo .logo-tag{font-size:7.5px;margin-top:2px}
.copyright{left:832px;top:958px;font-size:8.5px;color:#777}
</style>
</head>
<body>

<header>
  <div class="abs logo">
    <div class="logo-mark"></div>
    <div>
      <div class="logo-name">AshmoorMedical</div>
      <div class="logo-tag">Immediate Family and Personal Care</div>
    </div>
  </div>
  <div class="abs top-links">Register<span>|</span>Login<span>|</span>Blog</div>
  <div class="abs social top"><i></i><i></i><i></i></div>
  <div class="abs phone">(214) 555 0147</div>
</header>

<nav class="abs navbar">
  <div class="stripe"></div>
  <ul>
    <li style="left:243px">HOME</li>
    <li style="left:336px">ABOUT</li>
    <li style="left:435px">SERVICES</li>
    <li style="left:551px">STAFF</li>
    <li style="left:642px">INSURANCE</li>
    <li style="left:775px">VIDEOS</li>
    <li style="left:878px">CONTACT US</li>
  </ul>
  <div class="stripe b"></div>
</nav>

<aside class="abs side">
  <ul>
    <li>Immediate Care</li>
    <li>Allergies</li>
    <li>Primary Care</li>
    <li>Women’s Health</li>
    <li>Medical Spa Treatments</li>
    <li>Men’s Health</li>
    <li>Weight Loss</li>
  </ul>
</aside>
<svg class="abs side-tail" width="28" height="20"><polygon points="0,0 26,0 26,19" fill="#0a5c9f"/></svg>

<section class="hero">
  <div class="abs hero-photo" role="img" aria-label="Photo of a smiling family of four"></div>
  <div class="abs hero-line" style="top:170px;font-size:32px">CONCIERGE-QUALITY</div>
  <div class="abs hero-line" style="top:216px;font-size:32px">HEALTHCARE</div>
  <div class="abs hero-line" style="top:263px;font-size:16px;font-weight:600">CONVIENIENT COMPREHENSIVE CARE</div>
  <div class="abs hero-line" style="top:290px;font-size:24px;font-weight:600">... FOR YOUR</div>
  <div class="abs hero-line" style="top:321px;font-size:37px;color:var(--green)">WHOLE FAMILY</div>
  <div class="abs dots"><i></i><i></i><i></i></div>
</section>

<section>
  <div class="abs block" style="left:217px">
    <h2>IT’S ABOUT <em>TIME</em></h2>
    <div class="icon" style="background:var(--sky)">
      <svg width="40" height="40" viewBox="0 0 40 40"><circle cx="20" cy="20" r="16" fill="none" stroke="#fff" stroke-width="3"/><path d="M20 10v11" stroke="#fff" stroke-width="3"/><circle cx="20" cy="22" r="3" fill="#fff"/></svg>
    </div>
    <p>Lorem ipsum dolor sit amet, consectetuer adipiscing elit, sed diam nonummy nibh euismod tincidunt ut laoreet</p>
    <span class="more">MORE</span>
  </div>
  <div class="abs block" style="left:479px">
    <h2>IT’S ABOUT <em>CHOICES</em></h2>
    <div class="icon" style="background:var(--green)">
      <svg width="56" height="60" viewBox="0 0 56 60"><rect x="25" y="30" width="5" height="28" fill="#fff"/><circle cx="28" cy="22" r="18" fill="none" stroke="#fff" stroke-width="4" stroke-dasharray="5 4"/></svg>
    </div>
    <p>dolore magna aliquam erat volutpat. Ut wisi enim ad minim veniam, quis nostrud exerci tation ullamcorper</p>
    <span class="more">MORE</span>
  </div>
  <div class="abs block" style="left:739px">
    <h2>IT’S ABOUT <em>YOU</em></h2>
    <div class="icon" style="background:var(--sky)">
      <svg width="50" height="30" viewBox="0 0 50 30"><circle cx="12" cy="9" r="5" fill="#fff"/><circle cx="38" cy="9" r="5" fill="#fff"/><circle cx="25" cy="7" r="6" fill="#fff"/><path d="M3 26a9 9 0 0 1 18 0zM29 26a9 9 0 0 1 18 0zM14 26a11 11 0 0 1 22 0z" fill="#fff"/></svg>
    </div>
    <p>suscipit lobortis nisl ut aliquip ex ea commodo consequat. Duis autem vel eum iriure dolor in hendrerit in</p>
    <span class="more">MORE</span>
  </div>
</section>

<section>
  <h1 class="abs about-title">ASHMOOR <em>MEDICAL</em></h1>
  <div class="abs about-sub">Immiediate Family and personal care</div>
  <p class="abs about-copy">Lorem ipsum dolor sit amet, consectetuer adipiscing elit, sed diam nonummy nibh euismod tincidunt ut laoreet dolore magna aliquam erat volutpat. Ut wisi enim ad minim veniam, quis nostrud exerci tation ullamcorper suscipit lobortis nisl ut aliquip ex ea commodo consequat. Duis autem vel eum iriure dolor in hendrerit in vulputate velit esse molestie consequat, vel illum dolore eu feugiat nulla facilisis at vero eros et accumsan et iusto odio dignissim qui blandit praesent luptatum zzril delenit augue duis dolore te feugait nulla facilisi.</p>
  <div class="abs doc-photo" role="img" aria-label="Portrait photo of the clinic's physician"></div>
  <div class="abs doc-name">Daniel R. Okafor, MD</div>
</section>

<footer>
  <div class="abs footer-stripe stripe"></div>
  <div class="abs footer-bg"></div>
  <div class="abs foot-links"><span>Home</span><span>About</span><span>Services</span><span>Staff</span><span>Insurance</span><span>Videos</span><span>Contact Us</span></div>
  <div class="abs counters">
    <div class="counter"><i></i><b>10k</b></div>
    <div class="counter"><i style="width:28px"></i><b>451</b></div>
  </div>
  <div class="abs social foot"><i></i><i></i><i></i></div>
  <div class="abs foot-logo">
    <div class="logo-mark"></div>
    <div>
      <div class="logo-name">AshmoorMedical</div>
      <div class="logo-tag">Immediate Family and Personal Care</div>
    </div>
  </div>
  <div class="abs copyright">Copyrights 2013. Ashmoor medical.com</div>
</footer>

</body>
</html>
```